Advertising company unique advertising platform

we need a logo design for a new company based in Australia Melbourne. We develop innovated advertising platform where consumer can use this platform to get regular discount, as business owner they can use this platform for free advertisement. Payment for this advertisement platform only payable every two weeks, when I generate revenue for their business

Industry/Entity Type

Advertising

Contact Information for Business Card

Dale Morven | Co-Founder |Managing Director
Suite 718 240 Wattlebrook Lane Melbourne Vic 3000

ABN 38 614 207 923
Tel: +61 0487 259 318 | Email: dale.morven@plivorantu.com

Font styles to use
Decorative
Script

Requirements
Must have
• Try few different design and some round corner business card
Should not have
• One round corner business card...try 4 different colour background not only black, make sure two side is designed. Be creative so imagine you are giving this to a client make sure has wow factor, if you can also try one design with engrave like all the logo, words look 3d feel
• The word Advertising Platform use attached file font

```html
<!DOCTYPE html>
<html lang="en">
<head>
<meta charset="utf-8">
<title>Plivorantu – Business Card</title>
<link rel="stylesheet" href="https://fonts.googleapis.com/css2?family=Roboto:wght@400;500&family=Roboto+Condensed:wght@700&display=swap">
<style>
  :root {
    --backdrop: #6e5646;
    --card: #262626;
    --accent-red: #e2492c;
    --accent-teal: #1fe0a9;
    --ink: #ffffff;
    --rule: #e8e8e8;
  }
  * { margin: 0; padding: 0; box-sizing: border-box; }
  html, body { width: 1200px; height: 960px; overflow: hidden; }
  body {
    position: relative;
    background: var(--backdrop);
    font-family: "Roboto", Arial, sans-serif;
    color: var(--ink);
  }
  .card {
    position: absolute;
    background: var(--card);
    border-radius: 22px;
  }
  .card--front { left: 315px; top: 113px; width: 597px; height: 344px; }
  .card--back  { left: 312px; top: 473px; width: 600px; height: 340px; }

  .brand-mark {
    position: absolute;
    display: flex;
    align-items: center;
    gap: 10px;
    font-family: "Roboto Condensed", Arial, sans-serif;
    font-weight: 700;
    color: var(--accent-teal);
    white-space: nowrap;
  }
  .brand-mark__dot { border-radius: 50%; background: var(--accent-red); flex: none; }
  .card--front .brand-mark { right: 32px; top: 100px; font-size: 28px; }
  .card--front .brand-mark__dot { width: 22px; height: 22px; }
  .card--back .brand-mark {
    left: 0; right: 0; top: 118px; justify-content: center; font-size: 44px;
  }
  .card--back .brand-mark__dot { width: 34px; height: 34px; }

  .holder { position: absolute; left: 32px; top: 138px; }
  .holder__name {
    font-family: "Roboto Condensed", Arial, sans-serif;
    font-weight: 700;
    font-size: 21px;
    color: var(--accent-red);
    line-height: 24px;
  }
  .holder__role {
    font-size: 15px;
    font-weight: 500;
    color: var(--accent-teal);
    line-height: 19px;
  }
  .rule {
    position: absolute; left: 32px; right: 32px; top: 209px;
    height: 1px; background: var(--rule);
  }
  .contact { position: absolute; left: 32px; top: 218px; font-size: 14.5px; line-height: 18px; }
  .contact__row { display: flex; align-items: center; gap: 7px; }
  .contact__row svg { width: 13px; height: 13px; fill: var(--accent-red); flex: none; }
  .company { position: absolute; left: 32px; top: 259px; font-size: 14.5px; line-height: 18px; }
  .address { position: absolute; right: 31px; top: 259px; font-size: 14.5px; line-height: 18px; text-align: right; }

  .website {
    position: absolute; left: 0; right: 0; top: 294px;
    text-align: center; font-size: 14px; letter-spacing: 5px;
  }
</style>
</head>
<body>
  <section class="card card--front">
    <div class="brand-mark"><span class="brand-mark__dot"></span>Tellnova Exchange</div>

    <div class="holder">
      <p class="holder__name">DALE MORVEN</p>
      <p class="holder__role">CO-FOUNDER</p>
      <p class="holder__role">MANAGING DIRECTOR</p>
    </div>

    <div class="rule"></div>

    <div class="contact">
      <p class="contact__row">
        <svg viewBox="0 0 24 24" aria-hidden="true"><path d="M6.6 10.8a15.1 15.1 0 0 0 6.6 6.6l2.2-2.2a1 1 0 0 1 1-.25 11.4 11.4 0 0 0 3.6.57 1 1 0 0 1 1 1V20a1 1 0 0 1-1 1A17 17 0 0 1 3 4a1 1 0 0 1 1-1h3.5a1 1 0 0 1 1 1c0 1.25.2 2.45.57 3.57a1 1 0 0 1-.25 1z"/></svg>
        +61 0487 259 318
      </p>
      <p class="contact__row">
        <svg viewBox="0 0 24 24" aria-hidden="true"><path d="M2 5h20v14H2z M2 5l10 8 10-8" /></svg>
        dale.morven@plivorantu.com
      </p>
    </div>

    <div class="company">
      <p>Plivorantu</p>
      <p>ABN 38 614 207 923</p>
    </div>

    <div class="address">
      <p>Suite 718 240 Wattlebrook Lane</p>
      <p>Melbourne Vic 3000</p>
    </div>
  </section>

  <section class="card card--back">
    <div class="brand-mark"><span class="brand-mark__dot"></span>Tellnova Exchange</div>
    <p class="website">www.plivorantu.com</p>
  </section>
</body>
</html>
```